Business card

We need a business card design for our company based in Auckland , New Zealand called 'Ridge + Studio Ltd'. We provide architectural services. We would like to see designs that use the max. three colours (such as white, black, grey) The final design should communicate financial safety and growth."
Also I will provide our company logo. I would like to the logo to be embeded onto our business card.

Target Market(s)

new residential house, alteration & addition & light commericila design & drafting service

Industry/Entity Type

Architecture

Contact Information for Business Card

Company name: ridge + studio Ltd.
Name: Mark Delford
Job title: architectural designer & Design LBP
email address: mark@rplusd.co.nz
mobile number: 02 5163 2290
web site: www.rplusd.co.nz

Requirements
Must have
• My project must have..
• - embeded logo (attached company logo)
• I don't have a bigger version for our company logo, but I have one old one, so you can remove the word from it)
• - insert the attached small BKTW logo & LBP logo
• - creative, simple and clear business card.
• - Max. three colours
Nice to have
• - Here are the samples I would like to share with you: http://www.plimvora.com/blog/minimalistic-business-card-designs/
• I would like to have my business card like one of the creation.
Should not have
• TBA

```html
<!DOCTYPE html>
<html lang="en">
<head>
<meta charset="utf-8">
<title>Ridge + Studio Ltd — Business Card</title>
<link rel="stylesheet" href="https://fonts.googleapis.com/css2?family=Montserrat:wght@700&family=Open+Sans:wght@400;600&display=swap">
<style>
  :root {
    --backdrop: #3b3532;
    --card: #0b0b0b;
    --ink: #ffffff;
    --rule: #5a5a5a;
  }
  * { margin: 0; padding: 0; box-sizing: border-box; }
  html, body { width: 1200px; height: 900px; overflow: hidden; }
  body {
    background: var(--backdrop);
    display: flex;
    align-items: center;
    justify-content: center;
    gap: 50px;
    font-family: "Open Sans", sans-serif;
    color: var(--ink);
  }
  .card {
    position: relative;
    width: 530px;
    height: 310px;
    background: var(--card);
    box-shadow: 0 14px 30px rgba(0,0,0,.45);
  }

  /* Front */
  .brand {
    position: absolute;
    top: 62px;
    left: 0; right: 0;
    display: flex;
    flex-direction: column;
    align-items: center;
    gap: 16px;
  }
  .brand-dot {
    width: 46px; height: 46px;
    border-radius: 50%;
    background: var(--ink);
  }
  .brand-name {
    font-family: "Montserrat", sans-serif;
    font-weight: 700;
    font-size: 21px;
    letter-spacing: .3px;
  }
  .details {
    position: absolute;
    top: 186px;
    left: 0; right: 0;
    display: flex;
    justify-content: center;
  }
  .person {
    text-align: right;
    padding: 18px 22px 0 0;
    border-right: 1px solid var(--rule);
  }
  .person-name {
    font-family: "Montserrat", sans-serif;
    font-weight: 700;
    font-size: 19px;
    margin-bottom: 6px;
  }
  .person-role { font-size: 14.5px; line-height: 1.35; }
  .contacts {
    list-style: none;
    padding: 2px 0 14px 20px;
    font-size: 13.5px;
  }
  .contacts li {
    display: flex;
    align-items: center;
    gap: 10px;
    line-height: 26px;
  }
  .contacts svg { width: 12px; height: 12px; fill: var(--ink); flex: none; }

  /* Back */
  .back-mark {
    position: absolute;
    left: 48px;
    top: 50%;
    transform: translateY(-50%);
    display: flex;
    align-items: center;
    gap: 18px;
  }
  .back-mark .brand-dot { width: 60px; height: 60px; }
  .back-mark .brand-name { font-size: 22px; }
  .credentials {
    position: absolute;
    top: 28px;
    right: 30px;
    display: flex;
    flex-direction: column;
    align-items: flex-end;
    gap: 22px;
  }
  .membership {
    display: flex;
    align-items: center;
    gap: 8px;
  }
  .membership-badge {
    width: 40px; height: 30px;
    background: var(--ink);
  }
  .membership-label {
    font-weight: 600;
    font-size: 11px;
    line-height: 1.2;
  }
  .practitioner-badge {
    width: 70px; height: 70px;
    border-radius: 50%;
    background: var(--ink);
  }
</style>
</head>
<body>

  <section class="card card-front">
    <div class="brand">
      <span class="brand-dot"></span>
      <span class="brand-name">ridge + studio Ltd.</span>
    </div>
    <div class="details">
      <div class="person">
        <p class="person-name">Mark Delford</p>
        <p class="person-role">Architectural designer<br>&amp; Design LBP</p>
      </div>
      <ul class="contacts">
        <li>
          <svg viewBox="0 0 24 24" aria-hidden="true"><path d="M6.6 10.8a15.1 15.1 0 0 0 6.6 6.6l2.2-2.2a1 1 0 0 1 1-.25 11.4 11.4 0 0 0 3.6.57 1 1 0 0 1 1 1V20a1 1 0 0 1-1 1A17 17 0 0 1 3 4a1 1 0 0 1 1-1h3.5a1 1 0 0 1 1 1c0 1.25.2 2.45.57 3.57a1 1 0 0 1-.25 1z"/></svg>
          02 5163 2290
        </li>
        <li>
          <svg viewBox="0 0 24 24" aria-hidden="true"><path d="M2 5h20v14H2z M3.5 6.5 12 13l8.5-6.5" stroke="#0b0b0b" stroke-width="1.6"/></svg>
          mark@rplusd.co.nz
        </li>
        <li>
          <svg viewBox="0 0 24 24" aria-hidden="true"><circle cx="12" cy="12" r="10"/><path d="M2 12h20M12 2c3 3 3 17 0 20M12 2c-3 3-3 17 0 20" stroke="#0b0b0b" stroke-width="1.4" fill="none"/></svg>
          www.rplusd.co.nz
        </li>
      </ul>
    </div>
  </section>

  <section class="card card-back">
    <div class="back-mark">
      <span class="brand-dot"></span>
      <span class="brand-name">ridge + studio Ltd.</span>
    </div>
    <div class="credentials">
      <div class="membership">
        <span class="membership-badge" role="img" aria-label="Professional body membership badge"></span>
        <span class="membership-label">Professional<br>Member</span>
      </div>
      <span class="practitioner-badge" role="img" aria-label="Licensed practitioner badge"></span>
    </div>
  </section>

</body>
</html>
```